Seeking a new website design for electrical contracting company

Brisket & Vane electrical contracting needs a new website for brisket-vane.example

We are looking for modern and something real cool with motion for a landing page. we have some cool images from our photo shoot. maybe even 3d motion our existing logo. we would like something we can edit with news and events and update a past project page. Also allow to take payment
stock images at
https://lorapellwinphotos.picvault-demo.example/Brisket-and-Vane

Target Market(s)

construction , home owners , business owners,

Industry/Entity Type

construction , electrical

Coding

Number of Pages Required

5+ page

Font styles to use
Serif
Sans Serif

Colors
0054AA
0677BA
7BADD7
CADEEF
E8F1F8
0094D4
00A9DD
6FCCEA
C7EBF8
E9F6FB
FFF300
FFF600
FEFA6F
FFFEC7
FFFEE8

Requirements
Must have
• excitement, motion, selling professionalism,

```html
<!DOCTYPE html>
<html lang="en">
<head>
<meta charset="utf-8">
<title>Brisket &amp; Vane Electrical Contractors</title>
<link rel="stylesheet" href="https://fonts.googleapis.com/css2?family=League+Spartan:wght@500;600;700&family=Lato:wght@400;700&display=swap">
<style>
:root{
  --orange:#F28C1E;
  --orange-dark:#E07A10;
  --navy:#1F2A6B;
  --navy-deep:#18215A;
  --ink:#0E0F14;
  --text:#3A3D4A;
  --white:#FFFFFF;
}
*{box-sizing:border-box;margin:0;padding:0}
html,body{width:1200px;height:4542px;overflow:hidden}
body{font-family:"Lato",sans-serif;color:var(--text);background:var(--white);position:relative}
section,footer,header{position:absolute;left:0;width:1200px;overflow:hidden}
.abs{position:absolute}
.display{font-family:"League Spartan",sans-serif;font-weight:700;text-transform:uppercase;letter-spacing:.3px}
.eyebrow{font-family:"Lato",sans-serif;font-size:22px;color:var(--orange)}
.btn{position:absolute;display:flex;align-items:center;justify-content:center;background:var(--orange);color:var(--white);font-weight:700;font-size:15px;border-radius:2px}
.photo{position:absolute}

/* Hero */
.hero{top:0;height:645px;background:var(--ink)}
.hero-art{position:absolute;left:640px;top:0;width:560px;height:645px;background:radial-gradient(ellipse at 58% 45%,#f6b21e 0%,#c55a0c 25%,#3a1a08 55%,#0e0f14 80%)}
.brand{position:absolute;left:111px;top:34px;display:flex;align-items:center;gap:12px;color:var(--white)}
.brand-mark{width:70px;height:70px;border:5px solid var(--white);border-radius:50%}
.brand-name{font-family:"League Spartan",sans-serif;font-weight:700;font-size:32px;line-height:1;text-transform:uppercase}
.brand-sub{font-family:"League Spartan",sans-serif;font-weight:700;font-size:32px;line-height:1}
.nav{position:absolute;top:40px;left:515px;display:flex;gap:38px;font-size:14px;color:var(--white)}
.nav a{color:inherit;text-decoration:none;padding:4px 9px}
.nav a.active{background:var(--orange);border-radius:2px}
.hero h1{position:absolute;left:111px;top:182px;font-size:54px;line-height:68px;color:var(--white)}
.hero h1 span{color:var(--orange)}
.hero p{position:absolute;left:111px;top:400px;width:440px;font-size:19px;line-height:32px;color:var(--white)}

/* Services */
.services{top:645px;height:578px;background:var(--orange)}
.services .eyebrow{color:var(--white);position:absolute;left:111px;top:82px}
.services h2{position:absolute;left:111px;top:130px;font-size:31px;line-height:40px;color:var(--white)}
.services .lead{position:absolute;left:680px;top:78px;width:420px;font-size:18px;line-height:30px;color:var(--white)}
.card{position:absolute;top:259px;width:225px;height:233px;background:var(--navy);display:flex;flex-direction:column;align-items:center;text-align:center;color:var(--white)}
.card.light{background:var(--white);color:var(--navy)}
.card svg{margin-top:34px}
.card h3{font-family:"League Spartan",sans-serif;font-weight:500;font-size:18px;line-height:27px;margin-top:16px;padding:0 14px}
.card .more{color:var(--orange);font-weight:700;font-size:16px;margin-top:12px}

/* About */
.about{top:1223px;height:600px}
.about h2,.projects h2,.news h2{color:var(--navy)}
.about h2{position:absolute;left:643px;top:130px;font-size:32px;line-height:40px}
.about .eyebrow{position:absolute;left:643px;top:84px}
.about .copy{position:absolute;left:643px;top:238px;width:430px;font-size:14.5px;line-height:24px}
.about .copy p+p{margin-top:22px}

/* Projects */
.projects{top:1823px;height:719px}
.center{position:absolute;left:0;width:1200px;text-align:center}
.projects h2{font-size:31px}
.projects .intro{font-size:15px;line-height:24px}
.proj{position:absolute;top:194px;width:308px;text-align:center}
.proj .photo{position:relative;height:252px}
.proj h3{font-family:"League Spartan",sans-serif;font-weight:500;font-size:21px;color:var(--navy);margin-top:26px}
.proj p{font-size:14px;line-height:24px;margin-top:10px;padding:0 14px}
.proj .btn{position:relative;width:129px;height:35px;margin:22px auto 0}

/* CTA */
.cta{top:2542px;height:371px;background:var(--navy)}
.cta h2{color:var(--white);font-size:32px}
.cta .intro{color:var(--white);font-size:15px;line-height:24px}

/* News */
.news{top:2913px;height:623px}
.news .eyebrow{position:absolute;left:111px;top:106px}
.news h2{position:absolute;left:111px;top:150px;font-size:32px;line-height:40px}
.news h4{position:absolute;left:111px;top:252px;width:360px;font-size:17px;line-height:21px;color:var(--navy);font-weight:700}
.news .body{position:absolute;left:111px;top:322px;width:400px;font-size:14.5px;line-height:22.5px}

/* Testimonials */
.testi{top:3536px;height:575px;background:var(--orange)}
.testi .eyebrow{color:var(--white)}
.testi h2{color:var(--white);font-size:32px}
.testi .intro{color:var(--white);font-size:15px;line-height:23px}
.quote{position:absolute;top:236px;width:318px;height:226px;background:var(--navy);color:var(--white);padding:34px 24px 0}
.quote.light{background:var(--white);color:var(--text)}
.stars{display:flex;gap:2px}
.quote p{font-size:14.5px;line-height:22px;margin-top:18px}
.quote h5{font-size:17px;font-weight:700;margin-top:18px}
.quote.light h5{color:var(--navy)}
.quote small{font-size:12.5px;display:block;margin-top:4px}
.dots{position:absolute;top:488px;left:570px;display:flex;gap:6px}
.dots i{display:block;width:18px;height:5px;background:var(--white);border-radius:3px}
.dots i.on{background:var(--navy)}

/* Footer */
.footer{top:4111px;height:431px;background:var(--navy-deep);color:var(--white)}
.footer h6{position:absolute;top:76px;font-family:"League Spartan",sans-serif;font-weight:600;font-size:21px}
.footer .col{position:absolute;top:130px;font-size:14.5px;line-height:24px}
.footer ul{list-style:none}
.footer li{margin-bottom:14.5px}
.contact-row{display:flex;gap:22px;align-items:flex-start;margin-bottom:40px}
.social{position:absolute;left:111px;top:268px;display:flex;gap:16px}
.social span{width:30px;height:30px;border-radius:50%;border:2px solid var(--white)}
.social span.on{background:var(--white)}
.copyright{position:absolute;top:398px;left:0;width:1200px;text-align:center;font-size:12px}
</style>
</head>
<body>

<header class="hero">
  <div class="hero-art" role="img" aria-label="Glowing orange lightning bolt striking an electrical panel with sparks"></div>
  <svg class="abs" style="left:0;top:0" width="1200" height="645" viewBox="0 0 1200 645" aria-hidden="true">
    <polygon points="690,0 725,0 545,645 478,645" fill="#F28C1E"/>
    <polygon points="640,0 660,0 520,480 510,480" fill="#C9CCD6" opacity=".8"/>
  </svg>
  <div class="brand">
    <div class="brand-mark"></div>
    <div>
      <div class="brand-name">Brisket &amp; Vane</div>
    </div>
  </div>
  <nav class="nav">
    <a class="active">Home</a><a>About Us</a><a>Services</a><a>Projects</a><a>News &amp; Events</a><a>Contact</a>
  </nav>
  <h1 class="display">Bringing <span>Power</span><br><span>and Precision</span><br>to Every Project</h1>
  <p>High-performance electrical contracting for commercial, industrial, and mission-critical projects.</p>
  <a class="btn" style="left:111px;top:525px;width:165px;height:36px">Request a Quote</a>
</header>

<section class="services">
  <div class="eyebrow">Our Services</div>
  <h2 class="display">Scalable Power Solutions<br>Seamless Execution</h2>
  <p class="lead">From design to installation, we deliver reliable, code-compliant electrical systems built for performance. We handle complex electrical builds with expert planning, reliable installation, and long-term support.</p>

  <div class="card" style="left:111px">
    <svg width="66" height="66" viewBox="0 0 66 66" fill="none" stroke="#fff" stroke-width="2"><circle cx="33" cy="33" r="30"/><rect x="22" y="26" width="22" height="14" rx="3"/><path d="M27 26v-8M39 26v-8M33 40v12"/></svg>
    <h3>Commercial Electrical Contracting</h3><div class="more">Read More</div>
  </div>
  <div class="card light" style="left:363px">
    <svg width="66" height="66" viewBox="0 0 66 66" fill="none" stroke="#F28C1E" stroke-width="2"><circle cx="33" cy="33" r="30"/><circle cx="33" cy="29" r="13"/><path d="M35 20l-6 10h7l-6 10M28 44h10M29 49h8"/></svg>
    <h3>Industrial Electrical Solutions</h3><div class="more">Read More</div>
  </div>
  <div class="card" style="left:613px">
    <svg width="66" height="66" viewBox="0 0 66 66" fill="none" stroke="#fff" stroke-width="2"><path d="M36 14l-10 20h10l-8 18"/><path d="M14 33h6M46 33h6M20 18l4 4M46 18l-4 4M20 48l4-4M46 48l-4-4"/></svg>
    <h3>Emergency Power &amp; Generators</h3><div class="more">Read More</div>
  </div>
  <div class="card" style="left:863px">
    <svg width="66" height="66" viewBox="0 0 66 66" fill="none" stroke="#fff" stroke-width="2"><rect x="14" y="10" width="38" height="30" rx="2"/><rect x="19" y="15" width="28" height="20"/><path d="M34 17l-5 9h6l-4 7M22 40v12M33 40v14M44 40v12M16 52h12M38 52h12"/></svg>
    <h3>Power Distribution &amp; Panel Upgrades</h3><div class="more">Read More</div>
  </div>
</section>

<section class="about">
  <div class="photo" style="left:111px;top:86px;width:453px;height:435px;background:linear-gradient(160deg,#d7dade,#9aa3ad 55%,#e0763a)" role="img" aria-label="Electrician in orange safety gear on a ladder servicing a ceiling unit"></div>
  <div class="eyebrow">About Us</div>
  <h2 class="display">Powering Projects<br>Building Trust</h2>
  <div class="copy">
    <p>Brisket &amp; Vane is a full-service electrical contracting company delivering high-performance solutions across commercial, industrial, and mission-critical sectors.</p>
    <p>From initial planning through final inspection, we bring technical precision, skilled craftsmanship, and decades of field-tested experience to every project. Whether you're building new, upgrading infrastructure, or maintaining complex systems — we wire with purpose, integrity, and pride.</p>
  </div>
  <a class="btn" style="left:643px;top:482px;width:129px;height:38px">Read More</a>
</section>

<section class="projects">
  <div class="center eyebrow" style="top:18px">Past Projects</div>
  <h2 class="center display" style="top:56px">Projects That Speak for Themselves</h2>
  <p class="center intro" style="top:102px">Built for performance. Trusted for precision. We bring deep expertise, clean execution,<br>and serious attention to detail — powering commercial and industrial<br>projects that can't afford to fail.</p>

  <div class="proj" style="left:111px">
    <div class="photo" style="background:linear-gradient(180deg,#c9d8e8,#8b9aa8)" role="img" aria-label="Worker on a substation structure beneath a blue sky"></div>
    <h3>Commercial Projects</h3>
    <p>Lorem ipsum dolor sit amet, consectetur adipiscing elit, sed do eiusmod tempor incididunt ut labore et magna aliqua</p>
    <a class="btn">View All</a>
  </div>
  <div class="proj" style="left:446px">
    <div class="photo" style="background:linear-gradient(160deg,#b7bcc4,#6b5a4a 60%,#d86b2a)" role="img" aria-label="Two engineers in hard hats reviewing a laptop at an industrial plant"></div>
    <h3>Industrial Projects</h3>
    <p>Lorem ipsum dolor sit amet, consectetur adipiscing elit, sed do eiusmod tempor incididunt ut labore et magna aliqua</p>
    <a class="btn">View All</a>
  </div>
  <div class="proj" style="left:781px">
    <div class="photo" style="background:linear-gradient(160deg,#dfe2d8,#b9c07a 55%,#8e9a5a)" role="img" aria-label="Two electricians in high-visibility vests testing wiring"></div>
    <h3>Specialized Projects</h3>
    <p>Lorem ipsum dolor sit amet, consectetur adipiscing elit, sed do eiusmod tempor incididunt ut labore et magna aliqua</p>
    <a class="btn">View All</a>
  </div>
</section>

<section class="cta">
  <svg class="abs" style="left:0;top:0" width="1200" height="371" viewBox="0 0 1200 371" aria-hidden="true">
    <polygon points="35,0 60,0 135,190" fill="#C9CCD6" opacity=".85"/>
    <polygon points="80,0 95,0 130,120" fill="#C9CCD6" opacity=".6"/>
    <polygon points="980,120 1010,160 1175,371 1150,371" fill="#C9CCD6" opacity=".85"/>
    <polygon points="1040,190 1200,371 1185,371" fill="#C9CCD6" opacity=".7"/>
  </svg>
  <div class="center eyebrow" style="top:74px">Ready to Power Up?</div>
  <h2 class="center display" style="top:114px">Powering Your Future, Today</h2>
  <p class="center intro" style="top:160px">Expert electrical solutions for every project. Reliable, efficient, and built to last. Whether you're<br>planning a new build, upgrading systems, or need emergency electrical services, we're here<br>to bring your project to life. Let's get started today!</p>
  <a class="btn" style="left:514px;top:261px;width:172px;height:36px">Start Your Project</a>
</section>

<section class="news">
  <div class="eyebrow">News &amp; Events</div>
  <h2 class="display">Stay Updated with Our<br>Latest News &amp; Events</h2>
  <h4>Event 1: Powering the Future — Industry Conference 2025</h4>
  <p class="body">Whether it's a new project, an upcoming industry event, or important company news, you can find all the latest happenings here. Join us at this year's premier electrical industry event where we'll be showcasing our innovative solutions and sharing insights on the future of electrical contracting.</p>
  <a class="btn" style="left:111px;top:482px;width:129px;height:35px">View All</a>
  <div class="photo" style="left:634px;top:87px;width:453px;height:450px;background:radial-gradient(circle at 50% 50%,#a7a79e,#6e7270 60%,#3c4440)" role="img" aria-label="Crew in safety helmets and harnesses gathered in a circle in a training hall, seen from above"></div>
</section>

<section class="testi">
  <div class="center eyebrow" style="top:76px">Our Testimonials</div>
  <h2 class="center display" style="top:118px">What Our Clients Are Saying</h2>
  <p class="center intro" style="top:165px">We take pride in building lasting relationships and delivering<br>exceptional electrical services.</p>

  <div class="quote" style="left:111px">
    <div class="stars"><svg width="76" height="14" viewBox="0 0 76 14" fill="#F28C1E"><g id="s"><polygon points="7,0 9,5 14,5 10,8 11.5,13.5 7,10.5 2.5,13.5 4,8 0,5 5,5"/></g><use href="#s" x="15.5"/><use href="#s" x="31"/><use href="#s" x="46.5"/><use href="#s" x="62"/></svg></div>
    <p>Excepteur sint occaecat cupidatat non proident, sunt in culpa qui officia deserunt mollit anim id est laborum.</p>
    <h5>Hollings</h5><small>Apr 18 2025</small>
  </div>
  <div class="quote light" style="left:440px">
    <div class="stars"><svg width="76" height="14" viewBox="0 0 76 14" fill="#F28C1E"><use href="#s"/><use href="#s" x="15.5"/><use href="#s" x="31"/><use href="#s" x="46.5"/><use href="#s" x="62"/></svg></div>
    <p>Excepteur sint occaecat cupidatat non proident, sunt in culpa qui officia deserunt mollit anim id est laborum.</p>
    <h5>Dana</h5><small>Apr 18 2025</small>
  </div>
  <div class="quote" style="left:770px">
    <div class="stars"><svg width="76" height="14" viewBox="0 0 76 14" fill="#F28C1E"><use href="#s"/><use href="#s" x="15.5"/><use href="#s" x="31"/><use href="#s" x="46.5"/><use href="#s" x="62"/></svg></div>
    <p>Excepteur sint occaecat cupidatat non proident, sunt in culpa qui officia deserunt mollit anim id est laborum.</p>
    <h5>Rosalind</h5><small>Apr 18 2025</small>
  </div>
  <div class="dots"><i class="on"></i><i></i><i></i></div>
</section>

<footer class="footer">
  <h6 style="left:113px">About Us</h6>
  <h6 style="left:463px">Contact Us</h6>
  <h6 style="left:759px">Quick Links</h6>
  <h6 style="left:976px">Other Links</h6>

  <p class="col" style="left:113px;width:290px">Whether you're building new, upgrading infrastructure, or maintaining complex systems — we wire with purpose, integrity, and pride.</p>
  <div class="social"><span class="on"></span><span></span><span></span><span></span></div>

  <div class="col" style="left:463px">
    <div class="contact-row"><svg width="18" height="22" viewBox="0 0 18 22" fill="none" stroke="#fff" stroke-width="1.6"><path d="M9 21s7-7 7-12A7 7 0 0 0 2 9c0 5 7 12 7 12z"/><circle cx="9" cy="9" r="2.5"/></svg><span>82 Larchmere Rd.<br>Dovercliff NH 03999</span></div>
    <div class="contact-row"><svg width="18" height="18" viewBox="0 0 18 18" fill="none" stroke="#fff" stroke-width="1.6"><path d="M3 1h4l1.5 4-2 1.5a10 10 0 0 0 5 5l1.5-2 4 1.5v4a2 2 0 0 1-2 2A16 16 0 0 1 1 3a2 2 0 0 1 2-2z"/></svg><span>1-555-014-2290</span></div>
    <div class="contact-row"><svg width="18" height="14" viewBox="0 0 18 14" fill="none" stroke="#fff" stroke-width="1.6"><rect x="1" y="1" width="16" height="12"/><path d="M1 1l8 7 8-7"/></svg><span>hello@brisket-vane.example</span></div>
  </div>

  <ul class="col" style="left:759px"><li>Home</li><li>About Us</li><li>Services</li><li>Projects</li><li>News &amp; Events</li></ul>
  <ul class="col" style="left:976px"><li>FAQs</li><li>Support</li><li>Contact Us</li><li>Privacy Policy</li><li>Terms of Service</li></ul>

  <div class="copyright">Copyright © 2025 Brisket &amp; Vane electrical contracting. All rights reserved.</div>
</footer>

</body>
</html>
```